Fine Art business needs new website

We need a simple website with a home page, about us page, New sculptures, Sold sculptures, and a contact us page.Our sculptures are very high end one of a kind pieces. As such we need the site to be VERY elegant and professional. Lastly, because I'll be updating pictures on the website on a monthly basis it needs to be user friendly to update (Wordpress is preferred). The only branding we have so far for the business is a business card.
Updates
I wasn't completely ready when this project launched, also I am on the road right now and haven't been able to be as responsive to all you designers as I would like. I will work on giving feedback to all the top designs we've received so far. Thank you all so much for your participation and hardwork.
Target Market(s)
High end customers (affluent), art collectors, interior decorators/designers
Industry/Entity Type
Art Gallery
Coding
Coded - Design and coding required
Number of Pages Required
5+ page
Requirements
Must have
- Easily editable picture gallery for myself so that I can add new pieces(pictures of the pieces), remove sold pieces, etc. I would like the website to be built in wordpress so I can update it. I currently use mangewordpress through Netmarro for my other business website and would like to do the same for this one.
- Pages:
- -Intro page with featured pieces
- -Current pieces gallery (for sale) mainly a picture gallery
- -Sculptures archive (sold pieces) another picture gallery
- -About us: Pull-down of -about the artist (attached content)
- -Artistic Process (attached content)
- -Show Schedule:
- -one page dedicated to "friends of TMV" (basically a link page)
- TO BE CLEAR "www.pineroverslane.com" IS A TOTALLY DIFFERENT SITE AND I'M NOT TRYING TO COMBINE THE TWO OR JOIN THEM INTO ONE. This page needs be more elegant and seperate from the Pine Rovers site.
- UPDATE: I'd like a link to the TMV Faceplume page: https://www.faceplume-social.com/mirelcraftworks/
Nice to have
- I would like the pictures on the gallery pages able to have text connected with them (Materials, price)
- I would like the site style and fonts to be similar to our business cards we've already had designed (picture attached).
Should not have
- Too much flash or other things that will make the site slow to load.

```html
<!DOCTYPE html>
<html lang="en">
<head>
<meta charset="utf-8">
<title>Mirel Craftworks — Fine Stone Sculpture</title>
<link href="https://fonts.googleapis.com/css2?family=Cormorant+Garamond:wght@400;500;600&family=EB+Garamond:ital,wght@0,400;0,500;1,400&display=swap" rel="stylesheet">
<style>
:root{
  --paper:#ffffff;
  --ink:#2b2b2b;
  --ink-soft:#6d6d6d;
  --rule:#d9d9d9;
  --dot:#b9b9b9;
  --dot-active:#555555;
  --card:#121212;
  --footer:#1e1e1e;
  --footer-deep:#141414;
  --footer-text:#bdbdbd;
  --footer-head:#f2f2f2;
  --amethyst:#6b4a9a;
  --amethyst-deep:#2c1f48;
  --malachite:#1f6b52;
}
*{box-sizing:border-box;margin:0;padding:0}
html,body{width:1200px;height:3724px;overflow:hidden;background:var(--paper)}
body{position:relative;font-family:"EB Garamond",Georgia,serif;color:var(--ink)}
a{color:inherit;text-decoration:none}
.abs{position:absolute}

/* header */
.site-title{top:22px;left:0;width:1200px;text-align:center;font-family:"Cormorant Garamond",Georgia,serif;font-weight:500;font-size:40px;letter-spacing:3px}
.main-nav{top:86px;left:0;width:1200px;display:flex;justify-content:center;gap:34px;font-size:12px;letter-spacing:1.5px}
.main-nav a.current{border-bottom:1px solid var(--ink);padding-bottom:3px}

/* hero */
.hero{top:144px;left:32px;width:1136px;height:504px;background:#f4f3f6;overflow:hidden}
.hero-visual{position:absolute;inset:0;background:
  radial-gradient(ellipse 46% 34% at 36% 56%, #8a64c4 0%, #5a3c8c 45%, rgba(90,60,140,0) 75%),
  radial-gradient(ellipse 30% 22% at 72% 76%, #7c5bb0 0%, rgba(124,91,176,0) 70%),
  linear-gradient(180deg,#f7f6f8,#eceaf0)}
.hero-tagline{position:absolute;right:44px;top:112px;text-align:right;font-family:"Cormorant Garamond",Georgia,serif;font-size:30px;line-height:34px;letter-spacing:1.5px;color:#3a3a3a}

/* pager dots */
.dots{left:0;width:1200px;display:flex;justify-content:center;gap:9px}
.dots span{width:10px;height:10px;border-radius:50%;background:var(--dot)}
.dots span.on{background:var(--dot-active)}

.section-title{left:0;width:1200px;text-align:center;font-family:"Cormorant Garamond",Georgia,serif;font-size:26px;letter-spacing:2px;font-weight:500}
.gallery-link{left:0;width:1200px;text-align:center;font-size:13px;letter-spacing:1px}
.gallery-link span{border-bottom:1px solid var(--ink);padding-bottom:2px}

/* piece cards */
.piece{width:296px;height:392px;background:var(--card);overflow:hidden}
.piece-visual{position:absolute;inset:0}
.piece-label{position:absolute;left:14px;top:14px;background:rgba(255,255,255,.92);padding:6px 10px;font-size:10px;letter-spacing:1px;line-height:14px;color:#222;min-width:92px}
.piece-label .price{display:block;border-top:1px solid var(--rule);margin-top:3px;padding-top:2px}

/* videos */
.video{width:440px;height:400px;background:#0e0e0e;overflow:hidden}
.video-visual{position:absolute;inset:0}
.video-title{position:absolute;left:18px;top:16px;color:#fff;font-family:Arial,Helvetica,sans-serif;font-size:24px}
.video-play{position:absolute;left:180px;top:160px}

/* news */
.news{width:284px}
.news-visual{width:100%;height:256px}
.news-title{margin-top:36px;font-family:"Cormorant Garamond",Georgia,serif;font-size:20px;font-weight:600;line-height:23px}
.news-text{margin-top:10px;font-size:13px;line-height:17px;color:var(--ink-soft)}
.read-more{display:inline-block;margin-top:12px;font-size:13px;color:var(--ink);border-bottom:1px solid var(--ink)}

/* footer */
.site-footer{top:3304px;left:0;width:1200px;height:420px;background:var(--footer);color:var(--footer-text)}
.footer-col{position:absolute;top:46px;font-size:11px;line-height:15px}
.footer-col h3{font-family:"Cormorant Garamond",Georgia,serif;font-weight:600;font-size:19px;letter-spacing:1px;color:var(--footer-head);margin-bottom:18px}
.show{margin-bottom:10px}
.show em{display:block;color:#e6e6e6}
.footer-link{display:inline-block;border-bottom:1px solid var(--footer-text)}
.fb-post{width:180px;background:#f3f3f3;color:#333;padding:7px;margin-bottom:8px;font-size:9px;line-height:11px}
.fb-head{display:flex;align-items:center;gap:6px;margin-bottom:4px;font-weight:500}
.fb-head i{width:16px;height:16px;background:#888}
.socials{display:flex;gap:5px;margin-top:10px}
.socials i{width:14px;height:14px;background:#8a8a8a}
.newsletter{margin-top:22px}
.newsletter form{display:flex;margin-top:6px}
.newsletter .field{width:150px;height:22px;background:#fff}
.newsletter .send{width:44px;height:22px;background:#555;color:#fff;font-size:10px;line-height:22px;text-align:center}
.copyright{position:absolute;left:0;bottom:0;width:1200px;height:72px;background:var(--footer-deep);text-align:center;line-height:72px;font-size:11px;color:#8d8d8d}
</style>
</head>
<body>

<header>
  <div class="abs site-title">MIREL CRAFTWORKS</div>
  <nav class="abs main-nav">
    <a class="current" href="#">HOME</a><a href="#">ABOUT US</a><a href="#">CURRENT PIECES</a><a href="#">SCULPTURES ARCHIVE</a><a href="#">PINE ROVERS</a><a href="#">CONTACT US</a>
  </nav>
</header>

<section class="abs hero">
  <div class="hero-visual" role="img" aria-label="Large amethyst crystal sculpture on a pale background"></div>
  <p class="hero-tagline">BEAUTY AT ITS<br>HARDEST EXPRESSION</p>
</section>
<div class="abs dots" style="top:680px"><span class="on"></span><span></span><span></span></div>

<h2 class="abs section-title" style="top:764px">CURRENT PIECES</h2>
<article class="abs piece" style="top:836px;left:152px">
  <div class="piece-visual" role="img" aria-label="Amethyst geode slice sculpture on a stand" style="background:radial-gradient(ellipse 34% 40% at 50% 44%,#9b6cc9,#5c3d8a 55%,rgba(18,18,18,0) 80%),var(--card)"></div>
  <div class="piece-label">PRODUCT NAME<span class="price">$2,500</span></div>
</article>
<article class="abs piece" style="top:836px;left:456px">
  <div class="piece-visual" role="img" aria-label="Green malachite and quartz sculpture on a stand" style="background:radial-gradient(ellipse 30% 42% at 50% 46%,#3e9a76,#1f6b52 50%,rgba(18,18,18,0) 80%),var(--card)"></div>
  <div class="piece-label">PRODUCT NAME<span class="price">$3,200</span></div>
</article>
<article class="abs piece" style="top:836px;left:760px">
  <div class="piece-visual" role="img" aria-label="Tall crystal spire sculpture on a stand" style="background:radial-gradient(ellipse 22% 44% at 50% 46%,#cfcfd6,#7a7f8c 50%,rgba(18,18,18,0) 80%),var(--card)"></div>
  <div class="piece-label">PRODUCT NAME<span class="price">$1,900</span></div>
</article>
<div class="abs dots" style="top:1260px"><span class="on"></span><span></span><span></span><span></span></div>
<a class="abs gallery-link" style="top:1296px" href="#"><span>VIEW FULL GALLERY</span></a>

<h2 class="abs section-title" style="top:1400px">SCULPTURES ARCHIVE</h2>
<article class="abs piece" style="top:1472px;left:152px">
  <div class="piece-visual" role="img" aria-label="Spiral blue agate sculpture" style="background:radial-gradient(ellipse 24% 44% at 50% 46%,#7d8cc4,#3c4b84 50%,rgba(18,18,18,0) 80%),var(--card)"></div>
  <div class="piece-label">PRODUCT NAME<span class="price">SOLD</span></div>
</article>
<article class="abs piece" style="top:1472px;left:456px">
  <div class="piece-visual" role="img" aria-label="Amethyst cluster sculpture" style="background:radial-gradient(ellipse 30% 44% at 50% 46%,#8a5cc0,var(--amethyst-deep) 55%,rgba(18,18,18,0) 80%),var(--card)"></div>
  <div class="piece-label">PRODUCT NAME<span class="price">SOLD</span></div>
</article>
<article class="abs piece" style="top:1472px;left:760px">
  <div class="piece-visual" role="img" aria-label="Polished brown stone with crystal core" style="background:radial-gradient(ellipse 28% 44% at 50% 46%,#8a6a52,#4a3426 55%,rgba(18,18,18,0) 80%),var(--card)"></div>
  <div class="piece-label">PRODUCT NAME<span class="price">SOLD</span></div>
</article>
<div class="abs dots" style="top:1892px"><span class="on"></span><span></span><span></span><span></span></div>
<a class="abs gallery-link" style="top:1936px" href="#"><span>VIEW FULL GALLERY</span></a>

<h2 class="abs section-title" style="top:2016px">VIDEOS</h2>
<article class="abs video" style="top:2088px;left:152px">
  <div class="video-visual" role="img" aria-label="Coconut geode with glass video still" style="background:radial-gradient(ellipse 36% 44% at 50% 60%,#4a4e63,#1b1c24 60%,#0e0e0e)"></div>
  <p class="video-title">Coconut Geode with Glas...</p>
  <svg class="video-play" width="80" height="80" viewBox="0 0 80 80"><circle cx="40" cy="40" r="38" fill="rgba(255,255,255,.18)" stroke="#fff" stroke-width="2"/><path d="M32 25 L57 40 L32 55 Z" fill="#fff"/></svg>
</article>
<article class="abs video" style="top:2088px;left:608px">
  <div class="video-visual" role="img" aria-label="Amethyst coconut geode video still" style="background:radial-gradient(ellipse 36% 44% at 50% 60%,#5b3f80,#201733 60%,#0e0e0e)"></div>
  <p class="video-title">Amethyst Coconut Geod...</p>
  <svg class="video-play" width="80" height="80" viewBox="0 0 80 80"><circle cx="40" cy="40" r="38" fill="rgba(255,255,255,.18)" stroke="#fff" stroke-width="2"/><path d="M32 25 L57 40 L32 55 Z" fill="#fff"/></svg>
</article>
<div class="abs dots" style="top:2516px"><span class="on"></span><span></span><span></span><span></span></div>

<h2 class="abs section-title" style="top:2616px">NEWS</h2>
<article class="abs news" style="top:2688px;left:160px">
  <div class="news-visual" role="img" aria-label="Glowing geode sculpture on a dark stand" style="background:radial-gradient(ellipse 40% 46% at 50% 50%,#d98a3a,#5a3a6a 50%,#1a1a1a)"></div>
  <h3 class="news-title">Featured Sulptor</h3>
  <p class="news-text">Beautiful Brazilian agate stays on this piece, a graceful stone that grew slowly in the earth. Its rings catch the light in a quiet, warm glow...</p>
  <a class="read-more" href="#">Read More</a>
</article>
<article class="abs news" style="top:2688px;left:458px">
  <div class="news-visual" role="img" aria-label="Close view of a giant rough geode" style="background:linear-gradient(135deg,#c9a491,#9a7466 55%,#d8c2b6)"></div>
  <h3 class="news-title">Giant Moroccan Geode</h3>
  <p class="news-text">Acquired this stunning feather geode from a private collection of an old friend. One of the most striking pieces we have shown this year.</p>
  <a class="read-more" href="#">Read More</a>
</article>
<article class="abs news" style="top:2688px;left:756px">
  <div class="news-visual" role="img" aria-label="Purple amethyst crystals on display at a mineral show" style="background:linear-gradient(135deg,#b89bc9,#7a5a9c 55%,#c9b6d6)"></div>
  <h3 class="news-title">Verrin Gem and Mineral show 2017</h3>
  <p class="news-text">Our team at Pine Rovers returned from the show with new finds and we are ready to share more pieces with collectors.</p>
  <a class="read-more" href="#">Read More</a>
</article>
<div class="abs dots" style="top:3216px"><span class="on"></span><span></span><span></span><span></span></div>

<footer class="abs site-footer">
  <div class="footer-col" style="left:160px;width:200px">
    <h3>UPCOMING SHOWS</h3>
    <p class="show">Alder Ice Fest<em>August 2018</em></p>
    <p class="show">Highmoor Fine Art Show<em>July 2018</em></p>
    <p class="show">Redlake Park Arts and<br>Music Festival<em>June 2018</em></p>
    <p class="show">Cold Creek Festival<em>May 2018</em></p>
    <a class="footer-link" href="#">View All</a>
  </div>
  <div class="footer-col" style="left:380px;width:200px">
    <h3>UPCOMING EVENTS</h3>
    <p class="show">There are no upcoming events at<br>this time.</p>
    <a class="footer-link" href="#">View Calendar</a>
  </div>
  <div class="footer-col" style="left:608px;width:200px">
    <h3>FACEPLUME</h3>
    <div class="fb-post"><div class="fb-head"><i></i>Pine Rovers</div>New agate pieces arrived this week, come and see them in the studio.</div>
    <div class="fb-post"><div class="fb-head"><i></i>Pine Rovers</div>Thank you to everyone who visited us at the spring show. Great to meet so many collectors.</div>
    <a class="footer-link" href="#">Visit Faceplume Page</a>
  </div>
  <div class="footer-col" style="left:832px;width:220px">
    <h3>CONTACT US</h3>
    <p>Pine Rovers, PO Box 3316<br>Harlow Springs, CO 80462<br>(555) 014-2290<br>hello@pineroverslane.com<br>www.pineroverslane.com</p>
    <div class="socials"><i></i><i></i><i></i><i></i><i></i></div>
    <div class="newsletter">
      <h3 style="margin-bottom:4px">NEWSLETTER</h3>
      <form><span class="field"></span><span class="send">SEND</span></form>
    </div>
  </div>
  <div class="copyright">Copyright © 2017 Mirel Craftworks. All Rights Reserved.</div>
</footer>

</body>
</html>
```